Calvanto Group Real Estate Company business cards

New business card design, we are generally happy with the basic layout of the existing front of business card, (feel free to change) but require a head shot photo on the back side.

http://www.calvanto.com.au/

Attached logos, and existing business card

------------------------------

Target Market(s)

Real estate

Industry/Entity Type

Real Estate

Contact Information for Business Card

Standard size double sided

Font styles to use
Other font styles liked:
• Futura

Requirements
Must have
• Photo head shot on the back side
Nice to have
• yes
Should not have
• No

```html
<!DOCTYPE html>
<html lang="en">
<head>
<meta charset="utf-8">
<title>Calvanto Group – Business Cards</title>
<link href="https://fonts.googleapis.com/css2?family=Jost:wght@400;500;600&display=swap" rel="stylesheet">
<style>
  :root {
    --purple: #2e2566;
    --purple-deep: #231c52;
    --orange: #f39a1e;
    --ink: #3a3a4a;
    --muted: #8a8a96;
    --rule: #d9d9df;
    --paper: #ffffff;
    --backdrop: #e9e7e3;
  }
  * { box-sizing: border-box; margin: 0; padding: 0; }
  html, body { width: 1200px; height: 950px; overflow: hidden; }
  body {
    background: var(--backdrop);
    font-family: "Jost", "Futura", sans-serif;
    position: relative;
  }
  .card {
    position: absolute;
    left: 250px;
    width: 700px;
    height: 428px;
    overflow: hidden;
    box-shadow: 0 6px 18px rgba(0,0,0,.18);
  }
  .card--front { top: 31px; background: var(--paper); }
  .card--back { top: 491px; background: var(--purple); }

  /* front */
  .front-band { position: absolute; left: 0; bottom: 0; width: 700px; height: 428px; }
  .brand { position: absolute; left: 62px; top: 150px; }
  .brand__name {
    font-size: 58px; font-weight: 400; color: var(--purple);
    letter-spacing: 1px; line-height: 1;
  }
  .brand__sub {
    font-size: 11px; letter-spacing: 6px; color: var(--muted);
    text-align: right; margin-top: 4px; text-transform: uppercase;
  }
  .brand__services {
    margin-top: 14px; font-size: 15px; font-weight: 500;
    color: var(--purple); letter-spacing: 1px;
  }
  .brand__services span { color: var(--muted); margin: 0 8px; }
  .contact {
    position: absolute; left: 380px; top: 54px;
    padding-left: 26px; border-left: 1px solid var(--rule);
  }
  .contact__name { font-size: 26px; font-weight: 600; color: var(--purple); line-height: 1.1; }
  .contact__role { font-size: 17px; color: var(--orange); margin-bottom: 12px; }
  .contact__line { font-size: 14px; color: var(--ink); line-height: 1.55; }
  .contact__item { display: flex; align-items: center; gap: 8px; font-size: 14px; color: var(--ink); line-height: 1.6; }
  .contact__item svg { width: 13px; height: 13px; fill: var(--purple); flex: none; }

  /* back */
  .back-brand { position: absolute; left: 48px; top: 52px; display: flex; align-items: center; gap: 12px; }
  .back-brand__dot { width: 22px; height: 22px; background: var(--orange); }
  .back-brand__name { font-size: 40px; font-weight: 500; color: var(--orange); letter-spacing: 1px; }
  .back-web { position: absolute; left: 50px; top: 112px; font-size: 15px; color: #d7d3ee; letter-spacing: 1px; }
  .headshot {
    position: absolute; right: 40px; bottom: 0; width: 300px; height: 320px;
    background: radial-gradient(ellipse at 50% 35%, #c9a98a 0 22%, transparent 23%),
                linear-gradient(180deg, #3b3f5a 40%, #23263a 100%);
    border-radius: 150px 150px 0 0;
  }
</style>
</head>
<body>

<section class="card card--front" aria-label="Card front">
  <svg class="front-band" viewBox="0 0 700 428" aria-hidden="true">
    <path d="M0 418 C 260 410 520 360 700 250 L700 428 L0 428 Z" fill="var(--orange)"/>
    <path d="M0 428 C 270 420 530 372 700 266 L700 428 Z" fill="var(--purple)"/>
  </svg>

  <div class="brand">
    <div class="brand__name">calvanto</div>
    <div class="brand__sub">Group</div>
    <div class="brand__services">Buy<span>|</span>Sell<span>|</span>Rent</div>
  </div>

  <div class="contact">
    <div class="contact__name">Daniel Tran</div>
    <div class="contact__role">Director</div>
    <div class="contact__line">Calvanto Group</div>
    <div class="contact__line">ABN: 47 218 605 934</div>
    <div class="contact__item">
      <svg viewBox="0 0 24 24"><path d="M6.6 10.8a15.1 15.1 0 0 0 6.6 6.6l2.2-2.2a1 1 0 0 1 1-.25 11.4 11.4 0 0 0 3.6.57 1 1 0 0 1 1 1V20a1 1 0 0 1-1 1A17 17 0 0 1 3 4a1 1 0 0 1 1-1h3.5a1 1 0 0 1 1 1c0 1.25.2 2.45.57 3.57a1 1 0 0 1-.25 1z"/></svg>
      0400 555 318
    </div>
    <div class="contact__item">
      <svg viewBox="0 0 24 24"><path d="M2 5h20v14H2z M2 5l10 8 10-8" /></svg>
      danieltran@calvanto.com.au
    </div>
    <div class="contact__item">
      <svg viewBox="0 0 24 24"><circle cx="12" cy="12" r="10"/></svg>
      www.calvanto.com.au
    </div>
  </div>
</section>

<section class="card card--back" aria-label="Card back">
  <div class="back-brand">
    <div class="back-brand__dot"></div>
    <div class="back-brand__name">calvanto</div>
  </div>
  <div class="back-web">www.calvanto.com.au</div>
  <div class="headshot" role="img" aria-label="Head shot photo of the director in a dark suit and blue tie"></div>
</section>

</body>
</html>
```